For Lease Sign to Attract National Retail Tenants

Attached is a logo design that was created by Pixel Harbor. I will like to develop a leasing sign that is 4 foot wide by 4 foot high or 4 feet wide and 6 feet high. I would like the sign to have a black background and use the colors that are in the logo. These will be signs that are placed in front of shopping centers and are often read by passing motorist so the sign must be simple, clean, very easy to read, distinctive, and have as few words as possible. It would be good if small amounts of bright green can be added as a boarder or ????? The text should be FOR LEASE, 415-738-2916, Rod Kellaway. I will want to also design cards and letter head around the same theme.

Target Market(s)

National retail tenants wanting to lease space in my shopping centers

Industry/Entity Type

Real Estate Development

Contact Information for Business Card

Tall Oak Holdings, LLC Rod Kellaway President & CEO 4127 Marlow Ave. Suite 308 La Jolla, CA 92037 415-738-2916 rodkellaway@quillpost.net

```html
<!DOCTYPE html>
<html lang="en">
<head>
<meta charset="utf-8">
<title>Tall Oak Holdings — For Lease Sign</title>
<link rel="stylesheet" href="https://fonts.googleapis.com/css2?family=Figtree:wght@600;800&display=swap">
<style>
  :root {
    --sign-black: #0d0d0d;
    --frame-white: #f4f4f4;
    --brand-red: #e41e30;
    --brand-grey: #c9c9c9;
    --text-white: #ffffff;
  }
  html, body {
    margin: 0;
    padding: 0;
    width: 1200px;
    height: 1200px;
    overflow: hidden;
    background: var(--frame-white);
  }
  .lease-sign {
    position: relative;
    width: 1200px;
    height: 1200px;
    box-sizing: border-box;
    border: 16px solid var(--frame-white);
    background: var(--sign-black);
    font-family: "Figtree", "Helvetica Neue", Arial, sans-serif;
    color: var(--text-white);
    overflow: hidden;
  }
  .brand {
    position: absolute;
    top: 300px;
    left: 0;
    right: 0;
    display: flex;
    justify-content: center;
    align-items: center;
    gap: 28px;
  }
  .brand-mark {
    width: 64px;
    height: 64px;
    background: var(--brand-red);
  }
  .brand-name {
    font-weight: 600;
    font-size: 66px;
    letter-spacing: 2px;
    color: var(--brand-grey);
    text-transform: uppercase;
    white-space: nowrap;
  }
  .brand-suffix {
    font-size: 30px;
    margin-left: 10px;
  }
  .lease-band {
    position: absolute;
    left: 0;
    right: 0;
    top: 560px;
    height: 62px;
    background: var(--brand-red);
  }
  .lease-pill {
    position: absolute;
    top: 510px;
    left: 50%;
    transform: translateX(-50%);
    width: 640px;
    height: 160px;
    border-radius: 80px;
    background: var(--brand-red);
    display: flex;
    align-items: center;
    justify-content: center;
    font-weight: 800;
    font-size: 112px;
    letter-spacing: 1px;
    color: var(--text-white);
    white-space: nowrap;
  }
  .contact-name {
    position: absolute;
    top: 708px;
    left: 0;
    right: 0;
    text-align: center;
    font-weight: 800;
    font-size: 96px;
    white-space: nowrap;
  }
  .contact-phone {
    position: absolute;
    top: 850px;
    left: 0;
    right: 0;
    text-align: center;
    font-weight: 800;
    font-size: 168px;
    letter-spacing: 1px;
    white-space: nowrap;
  }
</style>
</head>
<body>
  <main class="lease-sign">
    <div class="brand">
      <span class="brand-mark" aria-hidden="true"></span>
      <span class="brand-name">Tall Oak Holdings<span class="brand-suffix">LLC</span></span>
    </div>
    <div class="lease-band" aria-hidden="true"></div>
    <div class="lease-pill">FOR LEASE</div>
    <div class="contact-name">Rod Kellaway</div>
    <div class="contact-phone">415-738-2916</div>
  </main>
</body>
</html>
```